IT Company based on Biology Business Needs a Professional Web Design

We need a professional business website design for a new company called 'Plume KEV'. We develop the machine learning solutions especially focused on deep learning algorithms for biology industry. Our initial product is a vision detection on biological images to help doctors diagnose the symptoms. We would like to see designs that use the color green.

Industry/Entity Type

Business

Number of Pages Required

5+ page

```html
<!DOCTYPE html>
<html lang="en">
<head>
<meta charset="utf-8">
<title>Plume KEV — Virtual Care Workflow Management</title>
<link href="https://fonts.googleapis.com/css2?family=Open+Sans:wght@300;400;600;700&display=swap" rel="stylesheet">
<style>
:root{
  --green:#1c9a4b;
  --sky:#34b1e6;
  --sky-soft:rgba(52,177,230,.85);
  --ink:#1e1e1e;
  --text:#444;
  --muted:#8a8a8a;
  --rule:#e6e6e6;
  --navy:#2f3552;
  --white:#fff;
}
*{box-sizing:border-box;margin:0;padding:0}
html,body{width:1200px;height:2250px;overflow:hidden;background:var(--white)}
body{font-family:"Open Sans",Arial,sans-serif;color:var(--text);position:relative}

.hero{position:absolute;left:0;top:0;width:1200px;height:592px;
  background:linear-gradient(100deg,#e9e4de 0%,#f7f5f2 35%,#ecebe8 60%,#d9d6d0 85%,#c9c4bc 100%)}
.site-header{position:absolute;left:0;top:0;width:1200px;height:110px}
.brand{position:absolute;left:72px;top:38px;font-size:26px;font-weight:400;color:var(--ink);letter-spacing:.2px}
.main-nav{position:absolute;left:384px;top:45px;display:flex;gap:27px;font-size:12px;color:#333}
.main-nav span.more::after{content:"";display:inline-block;margin-left:6px;vertical-align:middle;border:3px solid transparent;border-top-color:#333;border-bottom:0}
.login-icon{position:absolute;left:862px;top:44px}
.btn-start{position:absolute;left:903px;top:39px;width:124px;height:30px;background:var(--sky);color:var(--white);
  font-size:11px;text-align:center;line-height:30px;text-transform:uppercase}

.hero-title{position:absolute;left:172px;font-weight:300;color:var(--white);font-size:42px;background:var(--sky-soft);padding-left:26px}
.hero-title.line1{top:300px;width:285px;height:87px;line-height:82px}
.hero-title.line2{top:387px;width:512px;height:84px;line-height:78px}
.hero-intro{position:absolute;left:457px;top:300px;width:405px;height:86px;background:var(--white);
  padding:14px 18px;font-size:10.5px;line-height:1.35;color:#333}

.features-title{position:absolute;top:664px;width:1200px;text-align:center;font-size:39px;font-weight:300;color:var(--ink)}
.feature{position:absolute;width:225px;height:224px;border:1.5px solid var(--green);text-align:center;
  display:flex;flex-direction:column;align-items:center;justify-content:center;font-size:12px;line-height:1.3;color:#333}
.feature svg{margin-bottom:22px}
.feature.raised{justify-content:flex-start;padding-top:58px}
.feature .badge{position:absolute;top:-22px;left:50%;transform:translateX(-50%);background:var(--white);padding:0 10px}
.feature .badge svg{margin:0}
.feature .detail{margin-top:26px;font-size:10.5px;font-weight:700;color:#222;line-height:1.25;width:180px}

.divider{position:absolute;left:172px;top:1366px;width:855px;height:1px;background:var(--rule)}
.blog-title{position:absolute;top:1416px;width:1200px;text-align:center;font-size:30px;color:var(--ink);font-weight:400}
.post{position:absolute;top:1507px;width:172px}
.post-thumb{width:170px;height:113px;background:linear-gradient(180deg,#b9b39a 0%,#5a5448 45%,#2a2a2e 100%)}
.post-headline{margin-top:12px;font-size:10px;line-height:1.3;color:var(--sky)}
.post-meta{margin-top:10px;display:flex;align-items:center;gap:6px;font-size:9px;color:var(--muted)}
.post-meta .read{margin-left:10px;color:var(--sky);font-weight:700;font-size:10px}

.testimonial{position:absolute;left:0;top:1744px;width:1200px;height:428px;
  background:linear-gradient(90deg,#2a2f4a 0%,#343a58 45%,#3a405e 70%,#2d3350 100%)}
.testimonial .quote-icon{position:absolute;left:585px;top:88px}
.testimonial blockquote{position:absolute;top:170px;left:180px;width:840px;text-align:center;color:var(--white);
  font-size:22px;font-weight:300;line-height:1.42}
.testimonial cite{display:block;font-style:normal;color:var(--sky)}
.slider-dots{position:absolute;top:342px;left:584px;display:flex;gap:5px}
.slider-dots i{width:6px;height:6px;border:1px solid var(--white)}
.slider-dots i.active{background:var(--white)}

.site-footer{position:absolute;left:0;top:2172px;width:1200px;height:78px;background:var(--sky);color:var(--white)}
.copyright{position:absolute;left:237px;top:31px;font-size:12px}
.signup{position:absolute;left:805px;top:28px;font-size:13px;display:flex;align-items:center;gap:10px}
.social{position:absolute;left:936px;top:32px;display:flex;gap:24px}
.social i{width:14px;height:14px;border-radius:50%;background:var(--white)}
</style>
</head>
<body>

<section class="hero" role="img" aria-label="Photo of two doctors and a senior physician reviewing results on a screen"></section>

<header class="site-header">
  <div class="brand">Plume KEV</div>
  <nav class="main-nav">
    <span>Assessment</span><span>Admission</span><span>Care Planning</span><span>Orientation</span><span class="more">More</span>
  </nav>
  <svg class="login-icon" width="18" height="18" viewBox="0 0 18 18" fill="none" stroke="#34b1e6" stroke-width="1.4">
    <path d="M8 2h8v14H8"/><path d="M1 9h10M8 6l3 3-3 3"/>
  </svg>
  <div class="btn-start">Get Started</div>
</header>

<h1 class="hero-title line1">Virtual Care</h1>
<div class="hero-title line2">Workflow Management</div>
<p class="hero-intro">Lorem ipsum dolor sit amet, consectetur adipiscing elit. In ornare diam laoreet, cursus turpis eget, vehicula urna. Morbi bibendum nec ligula a tempus. Vivamus semper dapibus lacus et mollis. Nunc nec varius quam. Phasellus in tincidunt lectus.</p>

<h2 class="features-title">Vireo it’s..</h2>

<div class="feature" style="left:172px;top:781px">
  <svg width="52" height="40" viewBox="0 0 52 40" fill="#1c9a4b"><rect x="4" y="8" width="30" height="14" rx="7" transform="rotate(40 19 15)"/><rect x="20" y="14" width="28" height="14" rx="7" transform="rotate(-30 34 21)"/></svg>
  Rule engine with configurable<br>intervention steps
</div>
<div class="feature" style="left:487px;top:781px">
  <svg width="48" height="48" viewBox="0 0 48 48" fill="none" stroke="#1c9a4b" stroke-width="3"><circle cx="24" cy="24" r="21"/><circle cx="24" cy="24" r="7"/><path d="M14 24a10 10 0 0 1 10-10"/></svg>
  Knowledge<br>repository
</div>
<div class="feature" style="left:801px;top:781px">
  <svg width="46" height="50" viewBox="0 0 46 50" fill="#1c9a4b"><path d="M4 2h24l8 8v22a10 10 0 0 0-4-.8V12h-7V6H8v38h16a10 10 0 0 0 1.6 4H4z"/><circle cx="16" cy="20" r="5"/><rect x="11" y="30" width="14" height="3"/><rect x="11" y="36" width="10" height="3"/><circle cx="34" cy="41" r="8"/><path d="M30 41l3 3 5-6" stroke="#fff" stroke-width="2" fill="none"/></svg>
  We always<br>give a report
</div>
<div class="feature raised" style="left:172px;top:1065px">
  <span class="badge"><svg width="50" height="42" viewBox="0 0 50 42" fill="#1c9a4b"><rect x="2" y="2" width="46" height="30" rx="3"/><rect x="6" y="6" width="38" height="22" fill="#fff"/><rect x="6" y="6" width="38" height="22" fill="#1c9a4b"/><rect x="20" y="32" width="10" height="5"/><rect x="14" y="37" width="22" height="3"/></svg></span>
  Integrates with Electronic Records<br>and Paper Based Workflows
  <p class="detail">Lorem ipsum dolor sit amet, consectetur adipiscing elit. In ornare diam laoreet, cursus turpis eget, vehicula urna. Vivamus semper.</p>
</div>
<div class="feature" style="left:487px;top:1065px">
  <svg width="32" height="52" viewBox="0 0 32 52" fill="#1c9a4b"><rect x="2" y="2" width="28" height="48" rx="3"/><rect x="6" y="8" width="20" height="34" fill="#fff"/><circle cx="16" cy="46" r="2" fill="#fff"/><path d="M13 38V24a2 2 0 0 1 4 0v8h5v6z"/><path d="M10 22a7 7 0 0 1 12 0" fill="none" stroke="#1c9a4b" stroke-width="2"/></svg>
  Remote care through<br>mobile integration
</div>
<div class="feature" style="left:801px;top:1065px">
  <svg width="44" height="50" viewBox="0 0 44 50" fill="#1c9a4b"><circle cx="20" cy="12" r="10"/><path d="M0 48c0-14 8-22 20-22s20 8 20 22z"/><path d="M16 27l4 10 4-10" fill="#fff"/><circle cx="34" cy="40" r="8" fill="#fff"/><path d="M31 40h6M34 37v6" stroke="#1c9a4b" stroke-width="2.4"/></svg>
  Only the best and<br>qualified experts
</div>

<div class="divider"></div>
<h2 class="blog-title">Blog posts</h2>

<article class="post" style="left:172px">
  <div class="post-thumb" role="img" aria-label="Photo of three men in suits at an award ceremony"></div>
  <h3 class="post-headline">Norvale Labs CEO receives the<br>Aldren Foss award</h3>
  <div class="post-meta"><svg width="11" height="11" viewBox="0 0 12 12" fill="none" stroke="#8a8a8a"><circle cx="6" cy="6" r="5"/><path d="M6 3v3h2.5"/></svg>Fri, 06-02-2015<span class="read">READ MORE →</span></div>
</article>
<article class="post" style="left:399px">
  <div class="post-thumb" role="img" aria-label="Photo of three men in suits at an award ceremony"></div>
  <h3 class="post-headline">Norvale Labs CEO receives the<br>Aldren Foss award</h3>
  <div class="post-meta"><svg width="11" height="11" viewBox="0 0 12 12" fill="none" stroke="#8a8a8a"><circle cx="6" cy="6" r="5"/><path d="M6 3v3h2.5"/></svg>Fri, 06-02-2015<span class="read">READ MORE →</span></div>
</article>
<article class="post" style="left:625px">
  <div class="post-thumb" role="img" aria-label="Photo of three men in suits at an award ceremony"></div>
  <h3 class="post-headline">Norvale Labs CEO receives the<br>Aldren Foss award</h3>
  <div class="post-meta"><svg width="11" height="11" viewBox="0 0 12 12" fill="none" stroke="#8a8a8a"><circle cx="6" cy="6" r="5"/><path d="M6 3v3h2.5"/></svg>Fri, 06-02-2015<span class="read">READ MORE →</span></div>
</article>
<article class="post" style="left:855px">
  <div class="post-thumb" role="img" aria-label="Photo of three men in suits at an award ceremony"></div>
  <h3 class="post-headline">Norvale Labs CEO receives the<br>Aldren Foss award</h3>
  <div class="post-meta"><svg width="11" height="11" viewBox="0 0 12 12" fill="none" stroke="#8a8a8a"><circle cx="6" cy="6" r="5"/><path d="M6 3v3h2.5"/></svg>Fri, 06-02-2015<span class="read">READ MORE →</span></div>
</article>

<section class="testimonial" role="img" aria-label="Dimmed photo of medical staff consulting with a patient">
  <svg class="quote-icon" width="30" height="28" viewBox="0 0 30 28" fill="#fff"><path d="M0 0h30v20H12l-6 7v-7H0z"/><circle cx="9" cy="10" r="2" fill="#2f3552"/><circle cx="15" cy="10" r="2" fill="#2f3552"/><circle cx="21" cy="10" r="2" fill="#2f3552"/></svg>
  <blockquote>“Answer the questions that are asked. If you are writing to several organizations, you may find questions in each application that are similar. Do not be tempted to use the same statement for all applications.”<cite>- Author Name</cite></blockquote>
  <div class="slider-dots"><i></i><i></i><i class="active"></i></div>
</section>

<footer class="site-footer">
  <div class="copyright">Brindlework.com Copyright © 2015</div>
  <div class="signup"><svg width="16" height="16" viewBox="0 0 18 18" fill="none" stroke="#fff" stroke-width="1.4"><path d="M8 2h8v14H8"/><path d="M1 9h10M8 6l3 3-3 3"/></svg>Sign Up</div>
  <div class="social"><i></i><i></i><i></i></div>
</footer>

</body>
</html>
```